Velk Partners Building Business Cards

We need a business card that reflects our business as "Solar Experts" in San Diego. Browse our website www.velkpartners.example our License needs to be displayed as "CSLB# 3867140" our phone number is (619) 555-0187

Save thousands on your electric bills and increase the value of your home while helping to protect the environment. Our solar installation experts will help you design the system that's right for you, using only the highest quality equipment that will look great and give you ideal performance. Our goal is to make you energy independent, and get your electric bill to 0.

Paul Osterby
(619) 555-0187
paul@velkpartners.example

Target Market(s)

Home owners in san diego looking for solar

Industry/Entity Type

Solar Energy

Contact Information for Business Card

Paul Osterby
(619) 555-0187
paul@velkpartners.example

Font styles to use
Other font styles liked:
• Use our logo font

Requirements
Must have
• License needs to be displayed as "CSLB# 3867140" our phone number is (619) 555-0187
Nice to have
• Real images of rooftop home solar in san diego
Should not have
• our business address

```html
<!DOCTYPE html>
<html lang="en">
<head>
<meta charset="utf-8">
<title>Velk Partners Building — Business Cards</title>
<link href="https://fonts.googleapis.com/css2?family=Roboto:wght@400;500;700;900&display=swap" rel="stylesheet">
<style>
  :root {
    --stage: #a9a6a7;
    --navy: #2c4a8e;
    --navy-deep: #24407f;
    --ink: #1f3a78;
    --gold: #f0a91a;
    --white: #ffffff;
    --paper: #f7f7f6;
  }
  * { box-sizing: border-box; margin: 0; padding: 0; }
  html, body { width: 1200px; height: 1200px; overflow: hidden; }
  body {
    background: var(--stage);
    font-family: "Roboto", Arial, sans-serif;
    position: relative;
  }
  .card {
    position: absolute;
    width: 712px;
    height: 418px;
    border-radius: 26px;
    overflow: hidden;
  }
  /* Front */
  .card-front { left: 238px; top: 118px; background: var(--navy); color: var(--white); }
  .panel-photo {
    position: absolute; inset: 0;
    background: linear-gradient(160deg, #34539a 0%, #2b4889 50%, #263f7c 100%);
  }
  .front-name {
    position: absolute; left: 0; right: 0; top: 178px;
    text-align: center; font-weight: 700; font-size: 54px;
    letter-spacing: -1px; color: var(--white);
    transform: translateY(-100px);
  }
  .process-title {
    position: absolute; left: 0; right: 0; top: 206px;
    text-align: center; font-size: 22px; font-weight: 400;
    letter-spacing: 4px; color: var(--white);
  }
  .process-title::before, .process-title::after {
    content: ""; position: absolute; top: 13px; width: 55px; height: 3px;
    background: var(--gold); border-radius: 2px;
  }
  .process-title::before { left: 175px; }
  .process-title::after { left: 484px; }
  .process-line {
    position: absolute; left: 130px; width: 450px; top: 289px;
    border-top: 2px dotted var(--white);
  }
  .step {
    position: absolute; top: 252px; width: 140px; margin-left: -70px;
    text-align: center;
  }
  .step-icon {
    width: 78px; height: 76px; margin: 0 auto; background: var(--gold);
    display: flex; align-items: center; justify-content: center;
  }
  .step-icon svg { width: 44px; height: 44px; }
  .step-label {
    margin-top: 9px; font-size: 13.5px; line-height: 15px; color: var(--white);
  }
  /* Back */
  .card-back { left: 231px; top: 645px; background: var(--paper); color: var(--ink); }
  .back-name {
    position: absolute; left: 48px; top: 62px;
    font-weight: 700; font-size: 44px; letter-spacing: -1px; color: var(--ink);
  }
  .person { position: absolute; left: 49px; top: 232px; }
  .person-name { font-weight: 700; font-size: 26px; letter-spacing: -0.3px; }
  .person-role { font-size: 17px; margin-top: 4px; }
  .contact { position: absolute; left: 378px; top: 234px; font-size: 18.5px; }
  .contact-row { display: flex; align-items: center; height: 25px; }
  .contact-row svg { width: 18px; height: 18px; margin-right: 17px; flex: none; }
  .contact-row .accent { color: var(--gold); }
  .license { margin-top: 7px; font-size: 18.5px; }
</style>
</head>
<body>

<section class="card card-front">
  <div class="panel-photo" role="img" aria-label="Faint photo of rooftop solar panels in blue tones"></div>
  <div class="front-name" style="top:178px">Velk Partners Building</div>
  <h2 class="process-title">OUR PROCESS</h2>
  <div class="process-line"></div>

  <div class="step" style="left:131px">
    <div class="step-icon">
      <svg viewBox="0 0 44 44" fill="none" stroke="#24407f" stroke-width="3.5" stroke-linecap="round">
        <circle cx="18" cy="18" r="10"/><line x1="26" y1="26" x2="36" y2="36" stroke-width="5"/>
      </svg>
    </div>
    <p class="step-label">Site<br>Evaluation</p>
  </div>

  <div class="step" style="left:281px">
    <div class="step-icon">
      <svg viewBox="0 0 44 44" fill="none" stroke="#24407f" stroke-width="3" stroke-linejoin="round">
        <path d="M10 12 L16 6 L36 28 L38 38 L28 35 Z"/><line x1="10" y1="12" x2="30" y2="34"/>
      </svg>
    </div>
    <p class="step-label">Design &amp;<br>Permitting</p>
  </div>

  <div class="step" style="left:431px">
    <div class="step-icon">
      <svg viewBox="0 0 44 44">
        <rect x="8" y="8" width="28" height="18" rx="2" fill="#24407f" transform="rotate(-12 22 17)"/>
        <rect x="4" y="16" width="32" height="20" rx="2" fill="#24407f" stroke="#f0a91a" stroke-width="1.5"/>
        <rect x="8" y="28" width="9" height="3" fill="#f0a91a"/>
      </svg>
    </div>
    <p class="step-label">Purchase of<br>Materials</p>
  </div>

  <div class="step" style="left:582px">
    <div class="step-icon">
      <svg viewBox="0 0 44 44" fill="none" stroke="#24407f" stroke-linecap="round">
        <line x1="8" y1="36" x2="32" y2="12" stroke-width="4"/>
        <path d="M30 6 L38 14 L34 16 L28 10 Z" fill="#24407f" stroke-width="2"/>
        <line x1="12" y1="10" x2="34" y2="34" stroke-width="4"/>
        <circle cx="10" cy="8" r="4" stroke-width="3"/>
      </svg>
    </div>
    <p class="step-label">Installation &amp;<br>Commissioning</p>
  </div>
</section>

<section class="card card-back">
  <div class="back-name">Velk Partners Building</div>

  <div class="person">
    <p class="person-name">Paul Osterby</p>
    <p class="person-role">Managing Director</p>
  </div>

  <div class="contact">
    <div class="contact-row">
      <svg viewBox="0 0 18 18" fill="#f0a91a"><path d="M2 6 Q9 1 16 6 L14 8 L12 6 L6 6 L4 8 Z"/><rect x="4" y="9" width="10" height="7" rx="1"/></svg>
      <span>(619) 555-0187</span>
    </div>
    <div class="contact-row">
      <svg viewBox="0 0 18 18" fill="none" stroke="#f0a91a" stroke-width="1.6"><circle cx="9" cy="9" r="7"/><ellipse cx="9" cy="9" rx="3" ry="7"/><line x1="2" y1="9" x2="16" y2="9"/></svg>
      <span>paul@velkpartners.example</span>
    </div>
    <div class="contact-row">
      <svg viewBox="0 0 18 18"><rect x="1" y="4" width="16" height="11" fill="#f0a91a"/><path d="M1 4 L9 10 L17 4" fill="none" stroke="#fff" stroke-width="1.3"/></svg>
      <span>www.<span class="accent">velkpartners</span>.example</span>
    </div>
    <p class="license" style="margin-left:-35px">License: CSLB# 3867140</p>
  </div>
</section>

</body>
</html>
```